I would like to modify/update my 2 step login screen

I want a more modern looking login page for our document imaging application. I need to keep all of the same elements and buttons that currently exist. The first 2 screens are the login. The 3rd is a screenshot of the actual application home page.

```html
<!DOCTYPE html>
<html lang="en">
<head>
<meta charset="utf-8">
<title>Classic Login – States</title>
<link rel="stylesheet" href="https://fonts.googleapis.com/css2?family=Inter:wght@400;500;600;700&display=swap">
<style>
:root{
  --board:#efefef;
  --page:#fafafa;
  --header:#3b3b3d;
  --header-muted:#9a9a9c;
  --white:#ffffff;
  --line:#e4e4e4;
  --field-line:#dadada;
  --ink:#2a2a2a;
  --ink-soft:#555555;
  --placeholder:#9a9a9a;
  --green:#4cb050;
  --disabled:#d2d2d2;
  --error:#e06262;
  --lock-blue:#2f6ea8;
  --mark-grey:#b9b9b9;
  --mark-dark:#1e1e1e;
}
*{box-sizing:border-box;margin:0;padding:0}
html,body{width:1200px;height:482px;overflow:hidden;background:var(--board)}
body{font-family:"Inter",Arial,sans-serif;color:var(--ink)}
.board{position:relative;width:2576px;height:1036px;transform:scale(0.46584);transform-origin:0 0}
.screen{position:absolute;width:797px;height:447px;background:var(--page);overflow:hidden}
.screen.c1{left:46px}.screen.c2{left:889px}.screen.c3{left:1732px}
.screen.r1{top:47px}.screen.r2{top:541px}

.site-header{height:56px;background:var(--header);display:flex;align-items:center;justify-content:space-between;padding:0 19px 0 20px}
.brand{display:flex;align-items:center;gap:7px;color:var(--white);font-size:11px;font-weight:700;letter-spacing:.3px}
.brand-square{width:14px;height:14px;background:var(--white)}
.header-meta{text-align:right;font-size:7px;line-height:13px}
.header-links{color:var(--white);font-weight:500}
.header-links .dot{margin:0 5px;color:var(--header-muted)}
.copyright{color:var(--header-muted)}

.login-card{position:absolute;left:212px;top:93px;width:373px;background:var(--white);border:1px solid var(--line);border-radius:4px}
.login-card.has-error{border-bottom:none}
.tabs{display:flex;height:37px;border-bottom:1px solid var(--line)}
.tab{flex:1;display:flex;align-items:center;justify-content:center;position:relative}
.tab.active::after{content:"";position:absolute;left:0;right:0;bottom:-1px;height:3px;background:var(--green)}
.mark-circle{width:13px;height:13px;border-radius:50%;background:var(--mark-grey)}
.mark-square{width:13px;height:13px;background:var(--mark-grey)}
.mark-dark{width:13px;height:13px;border-radius:50%;background:var(--mark-dark)}
.card-body{padding:18px 46px 19px 46px}
.card-title{font-size:14px;line-height:18px;font-weight:600;color:var(--ink)}

.field{display:flex;align-items:center;height:25px;border:1px solid var(--field-line);border-radius:3px;padding:0 7px;gap:7px;font-size:7.5px;background:var(--white)}
.field.focus{border-color:var(--green)}
.field.invalid{border-color:var(--error)}
.field .value{flex:1;color:var(--ink)}
.field .placeholder{flex:1;color:var(--placeholder)}
.field .dots{flex:1;font-size:9px;letter-spacing:.5px;color:var(--ink)}
.caret{border-right:1px solid var(--ink);padding-right:1px}
.field-sep{width:1px;height:12px;background:var(--field-line)}
.icon{width:11px;height:11px;flex:none;color:var(--ink-soft)}
.icon.small{width:9px;height:9px;color:var(--placeholder)}
.db-field{margin-top:19px}
.stack .field + .field{margin-top:8px}

.actions{display:flex;align-items:center;justify-content:space-between;margin-top:19px}
.actions.end{justify-content:flex-end}
.btn{height:23px;border-radius:3px;color:var(--white);font-size:7.5px;font-weight:600;letter-spacing:.3px;display:flex;align-items:center;justify-content:center;background:var(--green)}
.btn.next{width:50px}.btn.login{width:54px}
.btn.disabled{background:var(--disabled)}
.forgot{color:var(--green);font-size:7.5px;font-weight:500}

.db-row{display:flex;align-items:center;height:14px;margin-top:19px;font-size:7.5px;gap:8px}
.db-row .divider{width:1px;height:12px;background:var(--field-line)}
.db-row b{font-weight:600}
.credentials{margin-top:20px}

.error-bar{height:22px;margin:0 -1px -1px;background:var(--error);color:var(--white);font-size:6.5px;display:flex;align-items:center;justify-content:center;border-radius:0 0 4px 4px}

.notice{position:absolute;left:0;right:0;text-align:center;font-size:7.5px;line-height:12px;color:var(--ink-soft)}
.notice b{color:var(--ink);font-weight:600}
</style>
</head>
<body>
<svg width="0" height="0" style="position:absolute">
  <defs>
    <symbol id="i-lock" viewBox="0 0 12 12"><rect x="2" y="5.2" width="8" height="6" rx="1" fill="currentColor"/><path d="M3.8 5.2V3.6a2.2 2.2 0 0 1 4.4 0v1.6" fill="none" stroke="currentColor" stroke-width="1.3"/></symbol>
    <symbol id="i-lock-line" viewBox="0 0 12 12"><rect x="2.5" y="5.2" width="7" height="5.8" rx="1" fill="none" stroke="currentColor" stroke-width="1"/><path d="M4 5.2V3.6a2 2 0 0 1 4 0v1.6" fill="none" stroke="currentColor" stroke-width="1"/></symbol>
    <symbol id="i-db" viewBox="0 0 12 12"><rect x="1.5" y="2" width="9" height="3.4" rx="1" fill="none" stroke="currentColor" stroke-width="1"/><rect x="1.5" y="6.6" width="9" height="3.4" rx="1" fill="none" stroke="currentColor" stroke-width="1"/></symbol>
    <symbol id="i-user" viewBox="0 0 12 12"><circle cx="6" cy="4" r="2.3" fill="none" stroke="currentColor" stroke-width="1"/><path d="M1.8 11a4.2 4.2 0 0 1 8.4 0" fill="none" stroke="currentColor" stroke-width="1"/></symbol>
    <symbol id="i-clear" viewBox="0 0 12 12"><circle cx="6" cy="6" r="4.6" fill="none" stroke="currentColor" stroke-width="1"/><path d="M4.2 4.2l3.6 3.6M7.8 4.2L4.2 7.8" stroke="currentColor" stroke-width="1"/></symbol>
    <symbol id="i-eye-off" viewBox="0 0 12 12"><path d="M1 6s1.8-3.4 5-3.4S11 6 11 6 9.2 9.4 6 9.4 1 6 1 6z" fill="none" stroke="currentColor" stroke-width="1"/><circle cx="6" cy="6" r="1.5" fill="none" stroke="currentColor" stroke-width="1"/><path d="M2 10L10 2" stroke="currentColor" stroke-width="1"/></symbol>
    <symbol id="i-back" viewBox="0 0 12 12"><path d="M10.5 6H2M5 3L2 6l3 3" fill="none" stroke="currentColor" stroke-width="1"/></symbol>
  </defs>
</svg>

<main class="board">

  <!-- Step 1: empty -->
  <section class="screen r1 c1">
    <header class="site-header">
      <div class="brand"><span class="brand-square"></span>MERIDIAN DOCS</div>
      <div class="header-meta"><div class="header-links">Privacy<span class="dot">•</span>Remote Support<span class="dot">•</span>Contact Us</div><div class="copyright">Copyright 2007-2024 Meridian Docs Inc</div></div>
    </header>
    <div class="login-card">
      <nav class="tabs"><div class="tab active"><svg class="icon" style="color:var(--lock-blue)"><use href="#i-lock"/></svg></div><div class="tab"><span class="mark-circle"></span></div><div class="tab"><span class="mark-square"></span></div><div class="tab"><span class="mark-dark"></span></div></nav>
      <div class="card-body">
        <h1 class="card-title">Classic Login</h1>
        <div class="field db-field"><svg class="icon"><use href="#i-db"/></svg><span class="placeholder">Database</span></div>
        <div class="actions end"><span class="btn next disabled">NEXT</span></div>
      </div>
    </div>
    <p class="notice" style="top:286px">All activity on this site is being recorded.<br>Your IP Address is being saved as '<b>192.168.168.134</b>'.</p>
  </section>

  <!-- Step 1: filled -->
  <section class="screen r1 c2">
    <header class="site-header">
      <div class="brand"><span class="brand-square"></span>MERIDIAN DOCS</div>
      <div class="header-meta"><div class="header-links">Privacy<span class="dot">•</span>Remote Support<span class="dot">•</span>Contact Us</div><div class="copyright">Copyright 2007-2024 Meridian Docs Inc</div></div>
    </header>
    <div class="login-card">
      <nav class="tabs"><div class="tab active"><svg class="icon" style="color:var(--lock-blue)"><use href="#i-lock"/></svg></div><div class="tab"><span class="mark-circle"></span></div><div class="tab"><span class="mark-square"></span></div><div class="tab"><span class="mark-dark"></span></div></nav>
      <div class="card-body">
        <h1 class="card-title">Classic Login</h1>
        <div class="field db-field focus"><svg class="icon"><use href="#i-db"/></svg><span class="value"><span class="caret">ABC12345</span></span><svg class="icon small"><use href="#i-clear"/></svg></div>
        <div class="actions end"><span class="btn next">NEXT</span></div>
      </div>
    </div>
    <p class="notice" style="top:286px">All activity on this site is being recorded.<br>Your IP Address is being saved as '<b>192.168.168.134</b>'.</p>
  </section>

  <!-- Step 1: error -->
  <section class="screen r1 c3">
    <header class="site-header">
      <div class="brand"><span class="brand-square"></span>MERIDIAN DOCS</div>
      <div class="header-meta"><div class="header-links">Privacy<span class="dot">•</span>Remote Support<span class="dot">•</span>Contact Us</div><div class="copyright">Copyright 2007-2024 Meridian Docs Inc</div></div>
    </header>
    <div class="login-card has-error">
      <nav class="tabs"><div class="tab active"><svg class="icon" style="color:var(--lock-blue)"><use href="#i-lock"/></svg></div><div class="tab"><span class="mark-circle"></span></div><div class="tab"><span class="mark-square"></span></div><div class="tab"><span class="mark-dark"></span></div></nav>
      <div class="card-body">
        <h1 class="card-title">Classic Login</h1>
        <div class="field db-field invalid"><svg class="icon"><use href="#i-db"/></svg><span class="value">ABC12345XYZ</span><svg class="icon small"><use href="#i-clear"/></svg></div>
        <div class="actions end"><span class="btn next">NEXT</span></div>
      </div>
      <div class="error-bar">Invalid database.</div>
    </div>
    <p class="notice" style="top:308px">All activity on this site is being recorded.<br>Your IP Address is being saved as '<b>192.168.168.134</b>'.</p>
  </section>

  <!-- Step 2: typing username -->
  <section class="screen r2 c1">
    <header class="site-header">
      <div class="brand"><span class="brand-square"></span>MERIDIAN DOCS</div>
      <div class="header-meta"><div class="header-links">Privacy<span class="dot">•</span>Remote Support<span class="dot">•</span>Contact Us</div><div class="copyright">Copyright 2007-2024 Meridian Docs Inc</div></div>
    </header>
    <div class="login-card">
      <nav class="tabs"><div class="tab active"><svg class="icon" style="color:var(--lock-blue)"><use href="#i-lock"/></svg></div><div class="tab"><span class="mark-circle"></span></div><div class="tab"><span class="mark-square"></span></div><div class="tab"><span class="mark-dark"></span></div></nav>
      <div class="card-body" style="padding-bottom:18px">
        <h1 class="card-title">Classic Login</h1>
        <div class="db-row"><svg class="icon small" style="color:var(--ink-soft)"><use href="#i-back"/></svg><span class="divider"></span><svg class="icon"><use href="#i-db"/></svg><span>Database: <b>ABC12345</b></span></div>
        <div class="stack credentials">
          <div class="field focus"><svg class="icon"><use href="#i-user"/></svg><span class="value"><span class="caret">john</span></span><svg class="icon small"><use href="#i-clear"/></svg></div>
          <div class="field"><svg class="icon"><use href="#i-lock-line"/></svg><span class="placeholder">Password</span><svg class="icon small"><use href="#i-eye-off"/></svg></div>
        </div>
        <div class="actions"><span class="forgot">Forgot Password?</span><span class="btn login disabled">LOGIN</span></div>
      </div>
    </div>
    <p class="notice" style="top:352px">All activity on this site is being recorded.<br>Your IP Address is being saved as '<b>192.168.168.134</b>'.</p>
  </section>

  <!-- Step 2: typing password -->
  <section class="screen r2 c2">
    <header class="site-header">
      <div class="brand"><span class="brand-square"></span>MERIDIAN DOCS</div>
      <div class="header-meta"><div class="header-links">Privacy<span class="dot">•</span>Remote Support<span class="dot">•</span>Contact Us</div><div class="copyright">Copyright 2007-2024 Meridian Docs Inc</div></div>
    </header>
    <div class="login-card">
      <nav class="tabs"><div class="tab active"><svg class="icon" style="color:var(--lock-blue)"><use href="#i-lock"/></svg></div><div class="tab"><span class="mark-circle"></span></div><div class="tab"><span class="mark-square"></span></div><div class="tab"><span class="mark-dark"></span></div></nav>
      <div class="card-body" style="padding-bottom:18px">
        <h1 class="card-title">Classic Login</h1>
        <div class="db-row"><svg class="icon small" style="color:var(--ink-soft)"><use href="#i-back"/></svg><span class="divider"></span><svg class="icon"><use href="#i-db"/></svg><span>Database: <b>ABC12345</b></span></div>
        <div class="stack credentials">
          <div class="field"><svg class="icon"><use href="#i-user"/></svg><span class="value">JohnDoe123</span><svg class="icon small"><use href="#i-clear"/></svg></div>
          <div class="field focus"><svg class="icon"><use href="#i-lock-line"/></svg><span class="dots"><span class="caret">●●●</span></span><svg class="icon small"><use href="#i-eye-off"/></svg><span class="field-sep"></span><svg class="icon small"><use href="#i-clear"/></svg></div>
        </div>
        <div class="actions"><span class="forgot">Forgot Password?</span><span class="btn login">LOGIN</span></div>
      </div>
    </div>
    <p class="notice" style="top:352px">All activity on this site is being recorded.<br>Your IP Address is being saved as '<b>192.168.168.134</b>'.</p>
  </section>

  <!-- Step 2: error -->
  <section class="screen r2 c3">
    <header class="site-header">
      <div class="brand"><span class="brand-square"></span>MERIDIAN DOCS</div>
      <div class="header-meta"><div class="header-links">Privacy<span class="dot">•</span>Remote Support<span class="dot">•</span>Contact Us</div><div class="copyright">Copyright 2007-2024 Meridian Docs Inc</div></div>
    </header>
    <div class="login-card has-error">
      <nav class="tabs"><div class="tab active"><svg class="icon" style="color:var(--lock-blue)"><use href="#i-lock"/></svg></div><div class="tab"><span class="mark-circle"></span></div><div class="tab"><span class="mark-square"></span></div><div class="tab"><span class="mark-dark"></span></div></nav>
      <div class="card-body" style="padding-bottom:18px">
        <h1 class="card-title">Classic Login</h1>
        <div class="db-row"><svg class="icon small" style="color:var(--ink-soft)"><use href="#i-back"/></svg><span class="divider"></span><svg class="icon"><use href="#i-db"/></svg><span>Database: <b>ABC12345</b></span></div>
        <div class="stack credentials">
          <div class="field invalid"><svg class="icon"><use href="#i-user"/></svg><span class="value">johndoe</span><svg class="icon small"><use href="#i-clear"/></svg></div>
          <div class="field invalid"><svg class="icon"><use href="#i-lock-line"/></svg><span class="dots">●●●●●●</span><svg class="icon small"><use href="#i-eye-off"/></svg><span class="field-sep"></span><svg class="icon small"><use href="#i-clear"/></svg></div>
        </div>
        <div class="actions"><span class="forgot">Forgot Password?</span><span class="btn login">LOGIN</span></div>
      </div>
      <div class="error-bar">Invalid username and/or password.</div>
    </div>
    <p class="notice" style="top:374px">All activity on this site is being recorded.<br>Your IP Address is being saved as '<b>192.168.168.134</b>'.</p>
  </section>

</main>
</body>
</html>
```